Corvell Keystone Lighting Commercial & Residential Landscape Lighting

Hello, I am looking for an Ad Design that I can use to promote ads on Plumora and other social media platforms. I want this ad to be a split screen ad meaning one photo at the top and one photo at the bottom to include a southern style home without outdoor landscape lighting & then the same picture at the bottom with outdoor landscape lighting. Add text to the graphic that talks about the difference landscape lighting does to your home. I want this ad to look professional and have professional design elements to the ad. I also have a logo I have uploaded below. We specialize in commercial grade outdoor landscape lighting, custom flag poles, outdoor audio, and we are locally and veteran owned. We offer lifetime warranty and quarterly maintenance on products.

```html
<!DOCTYPE html>
<html lang="en">
<head>
<meta charset="utf-8">
<title>Corvell Keystone Lighting – Before and After</title>
<link href="https://fonts.googleapis.com/css2?family=Playfair+Display:ital,wght@1,500&family=Inter+Tight:ital,wght@0,400;1,500&display=swap" rel="stylesheet">
<style>
  :root {
    --canvas: #1b1b1b;
    --ink: #ffffff;
    --gold: #8a6435;
    --gold-light: #f2b57a;
    --gold-deep: #d98e4a;
    --tick: #f0a45c;
    --dusk-top: #3f6ea8;
    --dusk-mid: #1f3140;
    --dusk-ground: #1c2a22;
    --night-top: #1a3a8c;
    --night-mid: #1d2535;
    --glow: #c98a45;
  }
  * { margin: 0; padding: 0; box-sizing: border-box; }
  html, body { width: 1200px; height: 1200px; overflow: hidden; background: var(--canvas); }
  .ad {
    position: relative;
    width: 1200px; height: 1200px;
    background:
      radial-gradient(ellipse 520px 340px at 1180px 20px, rgba(190,180,150,.28), transparent 70%),
      linear-gradient(150deg, transparent 40%, rgba(255,255,255,.05) 52%, transparent 62%),
      radial-gradient(ellipse 420px 300px at 0 1120px, rgba(160,140,100,.22), transparent 70%),
      var(--canvas);
    font-family: "Inter Tight", Arial, sans-serif;
    color: var(--ink);
    overflow: hidden;
  }
  .photo-frame { position: absolute; background: var(--gold); }
  .photo {
    position: absolute;
    border: 1.5px solid #f2f2f2;
  }
  .frame-before { left: 65px; top: 60px; width: 526px; height: 528px; }
  .photo-before {
    left: 78px; top: 75px; width: 521px; height: 526px;
    background:
      linear-gradient(180deg, var(--dusk-top) 0%, #2d4f78 18%, var(--dusk-mid) 32%, #8e949c 40%, #5d6068 50%, var(--dusk-ground) 62%, #1e2724 80%, #2e3a4a 100%);
  }
  .frame-after { left: 611px; top: 611px; width: 524px; height: 528px; }
  .photo-after {
    left: 599px; top: 599px; width: 524px; height: 526px;
    background:
      radial-gradient(ellipse 200px 110px at 50% 52%, rgba(230,170,90,.45), transparent 70%),
      radial-gradient(ellipse 260px 140px at 55% 75%, rgba(201,138,69,.35), transparent 70%),
      linear-gradient(180deg, var(--night-top) 0%, #12285e 18%, var(--night-mid) 32%, #5a4a3a 44%, #3a3226 55%, #1c2a1e 68%, #2a2a30 85%, #1e2840 100%);
  }
  .headline {
    position: absolute; left: 687px; top: 232px;
    font-family: "Playfair Display", Georgia, serif;
    font-style: italic; font-weight: 500;
    font-size: 80px; line-height: 1;
    background: linear-gradient(90deg, var(--gold-deep), var(--gold-light));
    -webkit-background-clip: text; background-clip: text;
    color: transparent;
  }
  .subline {
    position: absolute; left: 687px; top: 328px; width: 440px;
    font-style: italic; font-weight: 500;
    font-size: 31px; line-height: 44px; letter-spacing: -1.2px;
  }
  .benefits { position: absolute; left: 76px; top: 778px; list-style: none; }
  .benefit {
    position: relative; padding-left: 44px;
    font-size: 33px; line-height: 42px; letter-spacing: -1.3px;
    margin-bottom: 22px;
  }
  .tick { position: absolute; left: 0; bottom: 8px; width: 26px; height: 22px; }
</style>
</head>
<body>
<main class="ad">
  <div class="photo-frame frame-before"></div>
  <div class="photo photo-before" role="img" aria-label="Southern style white brick home at dusk without landscape lighting, dark walkway and shrubs"></div>

  <h1 class="headline">Elevates</h1>
  <p class="subline">The verall look and value of the home.</p>

  <ul class="benefits">
    <li class="benefit">Locally owned and<br>veteran-owned business.
      <svg class="tick" viewBox="0 0 26 22"><path d="M3 12 L10 18 L23 3" fill="none" stroke="var(--tick)" stroke-width="3.5" stroke-linecap="round" stroke-linejoin="round"/></svg></li>
    <li class="benefit">Lifetime warranty on products.
      <svg class="tick" viewBox="0 0 26 22"><path d="M3 12 L10 18 L23 3" fill="none" stroke="var(--tick)" stroke-width="3.5" stroke-linecap="round" stroke-linejoin="round"/></svg></li>
    <li class="benefit">Quarterly maintenance<br>included.
      <svg class="tick" viewBox="0 0 26 22"><path d="M3 12 L10 18 L23 3" fill="none" stroke="var(--tick)" stroke-width="3.5" stroke-linecap="round" stroke-linejoin="round"/></svg></li>
  </ul>

  <div class="photo-frame frame-after"></div>
  <div class="photo photo-after" role="img" aria-label="The same southern style home at night with warm landscape lighting along the walkway, shrubs and facade"></div>
</main>
</body>
</html>
```